Fitness Equipment Repair Business Needs a Catchy New Business Card

We have an existing business card, however, it is quite plain and boring. We are expanding primarily in the commercial area (gyms, studios, apartment complexes etc). The business card will serve as eye candy to those managers/owners that can't be met for a face to face.
Originally I was planning for a brochure as well, but all of our information is better summarized on our website. (brightloopservice.ca).
I would like the card to match the colour scheme of the website and utilize the logo. It should have a professional clean feel to it, however, a little colouring outside the lines wouldn't hurt.
The example card is for my service technician (Colin Marsh). If possible I would like to be able to edit the text to use for more than one person.

Industry/Entity Type

Appliance Repair

Contact Information for Business Card

Clean, crisp and professional but needs to be eye catching. Preferably using the black, white and red colour scheme matching the website. Double sided would be nice, but is not necessary.

Colors
ec1f27
ffffff
000000

Requirements
Must have
• Must be able to edit name, phone number and title to use for multiple people. Must show the company website (brightloopservice.ca).

```html
<!DOCTYPE html>
<html lang="en">
<head>
<meta charset="utf-8">
<title>Bright Loop Service – Business Card</title>
<link href="https://fonts.googleapis.com/css2?family=Cinzel:wght@400;500&family=Open+Sans:wght@400;600&family=Tinos:wght@700&display=swap" rel="stylesheet">
<style>
  :root {
    --red: #ec1f27;
    --deep-red: #b0141b;
    --white: #ffffff;
    --card-white: #f6f5f5;
    --black: #000000;
    --panel: #1c1c1c;
    --ink: #111111;
    --page: #e4e2e0;
  }
  * { margin: 0; padding: 0; box-sizing: border-box; }
  html, body { width: 1200px; height: 900px; overflow: hidden; background: var(--page); }
  .card {
    position: absolute; left: 100px; top: 164px;
    width: 1000px; height: 571px;
    border-radius: 26px; overflow: hidden;
    background: linear-gradient(135deg, var(--white), var(--card-white));
    box-shadow: 0 12px 40px rgba(0,0,0,.18);
    font-family: "Open Sans", sans-serif;
  }
  .panel-shape { position: absolute; inset: 0; width: 1000px; height: 571px; }
  .brand-mark {
    position: absolute; left: 66px; top: 118px;
    width: 128px; height: 128px; border-radius: 50%;
    background: var(--black);
  }
  .brand-name {
    position: absolute; left: 254px; top: 66px;
    font-family: "Cinzel", serif; font-weight: 400;
    font-size: 54px; line-height: 78px; color: var(--ink);
  }
  .person { position: absolute; left: 54px; top: 396px; }
  .person-name {
    font-family: "Cinzel", serif; font-weight: 500;
    font-size: 37px; color: var(--ink); letter-spacing: .5px;
  }
  .person-title { font-size: 25px; color: var(--ink); margin-left: 4px; margin-top: -2px; }
  .website {
    position: absolute; left: 54px; top: 527px;
    font-size: 25px; font-weight: 600; color: var(--deep-red);
  }
  .contact {
    position: absolute; right: 42px; top: 152px;
    color: var(--white); font-size: 24px; line-height: 38px; text-align: right;
  }
  .contact-line { display: flex; justify-content: flex-end; align-items: center; gap: 14px; }
  .contact-line svg { width: 20px; height: 20px; fill: var(--white); }
  .address { margin-top: 40px; margin-right: 34px; line-height: 36px; }
  .tagline {
    position: absolute; right: 46px; top: 438px;
    font-family: "Tinos", serif; font-weight: 700;
    font-size: 31px; line-height: 40px; color: var(--white); text-align: right;
  }
</style>
</head>
<body>
  <div class="card">
    <svg class="panel-shape" viewBox="0 0 1000 571" aria-hidden="true">
      <path d="M572,0 C548,150 628,262 548,362 C490,440 442,520 392,571 L1000,571 L1000,0 Z" fill="var(--red)"/>
      <path d="M585,0 C561,150 641,262 561,362 C503,440 455,520 405,571 L1000,571 L1000,0 Z" fill="var(--panel)"/>
    </svg>

    <div class="brand-mark" aria-hidden="true"></div>
    <div class="brand-name">Bright<br>Loop<br>Service</div>

    <div class="person">
      <div class="person-name">Colin Marsh</div>
      <div class="person-title">Managing Director</div>
    </div>
    <div class="website">www.brightloopservice.ca</div>

    <div class="contact">
      <div class="contact-line">044-555 010 234
        <svg viewBox="0 0 24 24"><path d="M6.6 10.8a15.1 15.1 0 0 0 6.6 6.6l2.2-2.2c.3-.3.7-.4 1-.2 1.1.4 2.3.6 3.6.6.6 0 1 .4 1 1V20c0 .6-.4 1-1 1A17 17 0 0 1 3 4c0-.6.4-1 1-1h3.5c.6 0 1 .4 1 1 0 1.3.2 2.5.6 3.6.1.3 0 .7-.2 1z"/></svg>
      </div>
      <div class="contact-line">044-555 010 234
        <svg viewBox="0 0 24 24"><path d="M8 1h8a2 2 0 0 1 2 2v18a2 2 0 0 1-2 2H8a2 2 0 0 1-2-2V3a2 2 0 0 1 2-2zm0 3v14h8V4zm4 15.5a1 1 0 1 0 0 2 1 1 0 0 0 0-2z"/></svg>
      </div>
      <div class="contact-line">info@brightloopservice.ca
        <svg viewBox="0 0 24 24"><path d="M2 5h20v14H2zm2 2v.4l8 5 8-5V7zm0 2.8V17h16V9.8l-8 5z"/></svg>
      </div>
      <div class="address">1234, Address Goes<br>Here, Country, 12345</div>
    </div>

    <div class="tagline">When your machines<br>stop mid-set,<br>we get them back in the game!</div>
  </div>
</body>
</html>
```